Hollow Thicket, a 3d voxel survival video game needs a card for gaming conventions

I am the lead developer for Hollow Thicket http://www.HollowThicket.example and need a business card to hand out at an indie gaming convention
The card would need to include the game name, website url, my name, position (Lead Developer), e-mail and phone number
The game is a 3d, voxel (with smooth terrain) based survival game with guns and wildlife. The main icon of the game would likely be a grizzly bear but I am willing to accept other designs too.
Attached is a media kit for the game with some images you can use but don't have to its just what little art I can provide. Anything on the website or from the video game can also be used. unrelated art can also be used.
Target Market(s)
Indie Developers/publishers at conferences
Industry/Entity Type
Games
Contact Information for Business Card
Name: Corin Waldrick
Position: Lead Developer
E-mail: Pale_Kettle@mailbox.example
Phone number: 555-372-1186

```html
<!DOCTYPE html>
<html lang="en">
<head>
<meta charset="utf-8">
<title>Hollow Thicket — Business Card</title>
<link rel="stylesheet" href="https://fonts.googleapis.com/css2?family=Open+Sans:wght@400;600;700&display=swap">
<style>
  :root {
    --stage: #e9e6e1;
    --card-black: #0c0b0b;
    --card-black-soft: #1b1a1a;
    --tan: #b79c63;
    --red: #a9170f;
    --red-bright: #c3261a;
    --white: #f2f0ec;
    --fur-dark: #6e4a30;
    --fur-light: #a87d56;
  }
  * { margin: 0; padding: 0; box-sizing: border-box; }
  html, body {
    width: 1200px;
    height: 900px;
    overflow: hidden;
    background: var(--stage);
    font-family: "Open Sans", Arial, sans-serif;
  }
  .sheet {
    position: relative;
    width: 1200px;
    height: 900px;
    display: flex;
    flex-direction: column;
    align-items: center;
    justify-content: center;
    gap: 36px;
  }
  .card {
    position: relative;
    width: 700px;
    height: 400px;
    overflow: hidden;
    background: radial-gradient(ellipse at 40% 35%, var(--card-black-soft), var(--card-black) 70%);
    box-shadow: 0 8px 22px rgba(0, 0, 0, 0.25);
  }
  .card__waves {
    position: absolute;
    inset: 0;
    width: 700px;
    height: 400px;
  }
  .card__mascot {
    position: absolute;
    left: 60px;
    top: 88px;
    width: 220px;
    height: 240px;
    border-radius: 46% 40% 18% 22% / 38% 40% 12% 14%;
    background: radial-gradient(ellipse at 55% 35%, var(--fur-light), var(--fur-dark) 75%);
  }
  .wordmark {
    position: absolute;
    font-weight: 700;
    color: var(--red-bright);
    letter-spacing: 4px;
    text-transform: uppercase;
    white-space: nowrap;
  }
  .card--front .wordmark {
    left: 300px;
    top: 128px;
    font-size: 38px;
  }
  .card--back .wordmark {
    left: 290px;
    top: 112px;
    font-size: 36px;
  }
  .holder {
    position: absolute;
    left: 62px;
    top: 52px;
  }
  .holder__name {
    font-size: 21px;
    font-weight: 600;
    text-transform: uppercase;
    letter-spacing: 0.5px;
    color: var(--tan);
  }
  .holder__first { color: var(--red-bright); }
  .holder__role {
    font-size: 15px;
    color: var(--white);
    margin-top: 2px;
  }
  .contact {
    position: absolute;
    left: 108px;
    top: 196px;
    list-style: none;
  }
  .contact__item {
    display: flex;
    align-items: center;
    gap: 9px;
    font-size: 17px;
    color: var(--white);
    line-height: 26px;
  }
  .contact__icon { width: 14px; height: 14px; flex: none; }
</style>
</head>
<body>
<main class="sheet">

  <section class="card card--front" aria-label="Card front">
    <svg class="card__waves" viewBox="0 0 700 400" aria-hidden="true">
      <defs>
        <linearGradient id="front-red" x1="0" y1="0" x2="1" y2="0">
          <stop offset="0" stop-color="#a9170f"/>
          <stop offset="0.55" stop-color="#b8321f"/>
          <stop offset="1" stop-color="#d99a6e"/>
        </linearGradient>
      </defs>
      <path d="M0,400 L0,322 C180,330 380,220 700,200 L700,400 Z" fill="#b79c63"/>
      <path d="M0,400 L0,352 C220,360 430,290 700,238 L700,400 Z" fill="#0c0b0b"/>
      <path d="M0,400 L0,360 C220,368 430,298 700,246 L700,400 Z" fill="url(#front-red)"/>
    </svg>
    <div class="card__mascot" role="img" aria-label="Photograph of a standing grizzly bear"></div>
    <p class="wordmark">Hollow Thicket</p>
  </section>

  <section class="card card--back" aria-label="Card back">
    <svg class="card__waves" viewBox="0 0 700 400" aria-hidden="true">
      <defs>
        <linearGradient id="back-red" x1="0" y1="0" x2="1" y2="0">
          <stop offset="0" stop-color="#a9170f"/>
          <stop offset="0.5" stop-color="#b8321f"/>
          <stop offset="1" stop-color="#d99a6e"/>
        </linearGradient>
      </defs>
      <path d="M0,400 L0,326 C200,338 420,200 700,170 L700,400 Z" fill="#b79c63"/>
      <path d="M0,400 L0,350 C240,360 450,274 700,220 L700,400 Z" fill="#0c0b0b"/>
      <path d="M0,400 L0,358 C240,368 450,282 700,228 L700,400 Z" fill="url(#back-red)"/>
    </svg>

    <div class="holder">
      <p class="holder__name"><span class="holder__first">Corin</span> Waldrick</p>
      <p class="holder__role">Lead Developer</p>
    </div>

    <p class="wordmark">Hollow Thicket</p>

    <ul class="contact">
      <li class="contact__item">
        <svg class="contact__icon" viewBox="0 0 14 14" aria-hidden="true">
          <path d="M2,5 C2,3 4,2 7,2 C10,2 12,3 12,5 L10,6 L9,4.5 L5,4.5 L4,6 Z" fill="#c3261a"/>
          <rect x="3" y="7" width="8" height="5" rx="1" fill="#c3261a"/>
        </svg>
        555-372-1186
      </li>
      <li class="contact__item">
        <svg class="contact__icon" viewBox="0 0 14 14" aria-hidden="true">
          <rect x="1" y="3" width="12" height="8" fill="#c3261a"/>
          <path d="M1,3 L7,8 L13,3" fill="none" stroke="#f2f0ec" stroke-width="1"/>
        </svg>
        Pale_Kettle@mailbox.example
      </li>
      <li class="contact__item">
        <svg class="contact__icon" viewBox="0 0 14 14" aria-hidden="true">
          <circle cx="7" cy="7" r="5.5" fill="none" stroke="#c3261a" stroke-width="1.4"/>
          <path d="M1.5,7 H12.5 M7,1.5 C4.5,4 4.5,10 7,12.5 M7,1.5 C9.5,4 9.5,10 7,12.5" fill="none" stroke="#c3261a" stroke-width="1"/>
        </svg>
        http://www.HollowThicket.example
      </li>
    </ul>
  </section>

</main>
</body>
</html>
```